i would like a business card to leave with customers and potential customers for electrical work and for the supply and install of reverse cycle airconditioning in the domestic and commercial market.
I own my own business and im a sole trader. I have an a'class electrical lisence and also a refrigeration lisence so i am
able to offer complete installations in airconditioning by a fully qualified and lisenced tradesman.
im looking for something that comes across as unique and professional.
i had the coluor black and some gold in mind but open to any coluors.
something like Lanterra Electrical & Refrigeration
or Lanterra Air.
i will use this design on a business card to advertise through summer to help generate installs through the busy season.

Target Market(s)

Mainly domestic house holds through summer who are in need of airconditioning and reliable information to acomadate thier cooling and heating requirements

Industry/Entity Type

Electrical

Requirements
Must have
• Business name- Lanterra
My name- Mark Delford
My mobile no- 0438 517 290
My email- mrdelford@qelvo.com.au
Installation & Decomissioning of aiconditioning split systems
LIC NO: TRK 540316
Nice to have
• Lanterra Electrical & Refrigeration

```html
<!DOCTYPE html>
<html lang="en">
<head>
<meta charset="utf-8">
<title>Lanterra Electrical &amp; Refrigeration – Business Card</title>
<link rel="stylesheet" href="https://fonts.googleapis.com/css2?family=Crimson+Text:wght@400;600&display=swap">
<style>
  :root {
    --backdrop: #2b3636;
    --card-black: #111111;
    --card-charcoal: #262626;
    --brand-red: #e2312a;
    --brand-red-deep: #a8150f;
    --text-light: #d6d6d6;
    --text-muted: #8c8c8c;
    --name-grey: #c9c9c9;
    --monogram: #2f2f2f;
    --badge: #f2f2f2;
  }
  * { margin: 0; padding: 0; box-sizing: border-box; }
  html, body {
    width: 1200px; height: 750px; overflow: hidden;
    background: var(--backdrop);
    font-family: "Crimson Text", Georgia, serif;
  }
  .canvas { position: relative; width: 1200px; height: 750px; }

  .card {
    position: absolute; top: 212px;
    width: 533px; height: 325px;
    overflow: hidden;
    box-shadow: 0 6px 18px rgba(0,0,0,.45);
  }

  /* Front */
  .card--front { left: 40px; background: linear-gradient(180deg, #151515 0%, #1f1f1f 60%, #111 100%); }
  .card__swoosh { position: absolute; inset: 0; }
  .brand-name {
    position: absolute; color: var(--brand-red);
    font-weight: 600; line-height: 1;
  }
  .card--front .brand-name { left: 22px; top: 22px; font-size: 58px; }
  .holder-name {
    position: absolute; right: 32px; top: 100px;
    font-size: 34px; color: var(--name-grey); font-weight: 400;
  }
  .contact-list {
    position: absolute; left: 28px; top: 155px;
    list-style: none; font-size: 18px; line-height: 24px;
  }
  .contact-list .label { color: var(--text-muted); }
  .contact-list .value { color: var(--text-light); }
  .service-line {
    position: absolute; left: 34px; top: 294px;
    font-size: 15.5px; color: var(--text-light);
  }
  .accreditation-badge {
    position: absolute; left: 471px; top: 264px;
    width: 43px; height: 49px; background: var(--badge);
  }

  /* Back */
  .card--back { left: 621px; background: linear-gradient(160deg, var(--card-charcoal) 0%, #1b1b1b 100%); }
  .monogram {
    position: absolute; left: -8px; top: 0; width: 100%;
    font-size: 300px; line-height: 1; letter-spacing: -6px;
    color: var(--monogram); font-weight: 400;
  }
  .card--back .brand-name {
    left: 0; right: 0; top: 112px; text-align: center; font-size: 60px;
  }
  .tagline {
    position: absolute; left: 0; right: 0; top: 280px; text-align: center;
    font-size: 20px; letter-spacing: 3px; color: var(--brand-red);
  }
</style>
</head>
<body>
<main class="canvas">

  <section class="card card--front" aria-label="Business card front">
    <svg class="card__swoosh" width="533" height="325" viewBox="0 0 533 325" aria-hidden="true">
      <defs>
        <linearGradient id="lowerPanel" x1="0" y1="0" x2="0" y2="1">
          <stop offset="0" stop-color="#3a3a3a"/>
          <stop offset="0.45" stop-color="#161616"/>
          <stop offset="1" stop-color="#0d0d0d"/>
        </linearGradient>
        <linearGradient id="redBand" x1="0" y1="0" x2="1" y2="0">
          <stop offset="0" stop-color="var(--brand-red-deep)"/>
          <stop offset="0.6" stop-color="var(--brand-red)"/>
          <stop offset="1" stop-color="#f0483f"/>
        </linearGradient>
      </defs>
      <path d="M0,272 C200,282 420,248 533,172 L533,325 L0,325 Z" fill="url(#lowerPanel)"/>
      <path d="M0,256 C210,268 420,232 533,152 L533,172 C420,248 200,282 0,272 Z" fill="url(#redBand)"/>
    </svg>

    <div class="brand-name">Lanterra</div>
    <h1 class="holder-name">Mark Delford</h1>
    <ul class="contact-list">
      <li><span class="label">mob:</span>&nbsp; <span class="value">0438 517 290</span></li>
      <li><span class="label">email:</span> <span class="value">mrdelford@qelvo.com.au</span></li>
      <li><span class="label">LIC No:</span> <span class="value">TRK 540316</span></li>
      <li><span class="label">LIC No:</span> <span class="value">L063817</span></li>
    </ul>
    <p class="service-line">Installation &amp; Decomissioning of airconditioning Split Systems</p>
    <div class="accreditation-badge" role="img" aria-label="Authorised installer badge"></div>
  </section>

  <section class="card card--back" aria-label="Business card back">
    <div class="monogram" aria-hidden="true">LER</div>
    <div class="brand-name">Lanterra</div>
    <p class="tagline">Lanterra Electrical &amp; Refrigeration</p>
  </section>

</main>
</body>
</html>
```